Meadow Kr Circle (company name is Meadow Kr Circle LLP)

management of homestay, hospitality something similar with https://www.dorvika.example

Target Market(s)

johor bahru market (Malaysia)

Contact Information for Business Card

Meadow Circle KR LLP

Logo Text

eyes catching, attractive, amazing, Nice, jaw dropping for design

Coding

Coded - Design and coding required

Number of Pages Required

5+ page

Colors

Designer to choose colors to be used in the design.

Requirements
Must have
• please change the short term proposal to our company logo and change the name from dorvika to meadow KR Circle LLP
• thanks
Nice to have
• please let me have eyes catching , jaw dropping design

```html
<!DOCTYPE html>
<html lang="en">
<head>
<meta charset="utf-8">
<title>Meadow Kr Circle – Short-Stay Management Proposal</title>
<link href="https://fonts.googleapis.com/css2?family=Montserrat:wght@400;500;600;700&family=Open+Sans:wght@400;600&display=swap" rel="stylesheet">
<style>
:root{
  --maroon:#5b1a0d;
  --maroon-dark:#3e1006;
  --ink:#1c1c1c;
  --text:#555;
  --grey-bg:#efefef;
  --footer:#0d0d0d;
  --white:#fff;
  --gold:#e8a11c;
}
*{box-sizing:border-box;margin:0;padding:0}
html,body{width:1200px;height:4255px;overflow:hidden;background:var(--white)}
body{font-family:"Montserrat",sans-serif;color:var(--ink);position:relative}
.abs{position:absolute}
/* header */
.site-header{position:absolute;top:0;left:0;width:1200px;height:86px;background:var(--white);display:flex;align-items:center;padding:0 110px;justify-content:space-between}
.brand{display:flex;align-items:center;gap:10px;font-weight:700;color:var(--maroon-dark);font-size:26px}
.brand-square{width:26px;height:26px;background:var(--maroon-dark)}
.main-nav{display:flex;gap:26px;align-items:center;font-size:15px;color:#444}
.main-nav .active{color:var(--maroon);font-weight:600}
/* hero */
.hero{position:absolute;top:86px;left:0;width:1200px;height:720px;overflow:hidden}
.hero-photo{position:absolute;inset:0;background:linear-gradient(180deg,#6f87a8 0%,#9aaec6 30%,#7b6a55 60%,#3f5a30 85%,#2d4422 100%)}
.hero-title{position:absolute;top:130px;left:0;width:100%;text-align:center;color:var(--white)}
.hero-brand{display:inline-flex;align-items:center;gap:16px;font-size:72px;font-weight:700}
.hero-brand .brand-square{width:60px;height:60px;background:var(--white)}
.hero-sub{font-size:44px;font-weight:500;margin-top:8px}
.hero-tag{font-size:30px;font-weight:600;margin-top:18px}
.slider-dots{position:absolute;right:58px;top:320px;display:flex;flex-direction:column;gap:10px}
.slider-dots span{width:11px;height:11px;border-radius:50%;background:var(--white)}
.slider-dots .on{box-shadow:0 0 0 3px rgba(255,255,255,.5)}
.hero-swoosh{position:absolute;left:0;bottom:0}
/* about */
.about-logo{position:absolute;top:918px;left:115px}
.about-photo{position:absolute;top:876px;left:550px;width:538px;height:372px;background:linear-gradient(160deg,#1b4f97 0%,#6a9fd6 45%,#e9eef2 60%,#274d80 100%);box-shadow:0 8px 20px rgba(0,0,0,.3)}
.about-box{position:absolute;top:1012px;left:115px;width:494px;height:360px;border:3px solid var(--maroon);padding:60px 40px 30px 40px;background:var(--white)}
.about-box h2{font-size:34px;font-weight:600;margin-bottom:14px}
.about-box p{font-family:"Open Sans",sans-serif;font-size:13.5px;line-height:1.85;color:var(--text);text-align:justify}
/* services */
.services-band{position:absolute;top:1468px;left:0;width:1200px;height:327px;background:linear-gradient(180deg,var(--maroon-dark),var(--maroon))}
.services-title{position:absolute;top:1530px;width:1200px;text-align:center;color:var(--white);font-size:33px;font-weight:600}
.service-card{position:absolute;top:1630px;width:312px;height:360px;background:var(--white);box-shadow:0 3px 12px rgba(0,0,0,.25);text-align:center}
.service-card .photo{margin:8px;height:156px}
.service-card h3{font-size:19px;font-weight:600;margin:22px 20px 12px;line-height:1.3}
.service-card p{font-family:"Open Sans",sans-serif;font-size:13.5px;line-height:1.75;color:var(--text);padding:0 30px}
/* steps */
.section-title{position:absolute;width:1200px;text-align:center;font-size:36px;font-weight:600}
.steps-intro{position:absolute;top:2160px;width:1200px;text-align:center;font-family:"Open Sans",sans-serif;font-size:14.5px;line-height:1.8;color:var(--text)}
.step{position:absolute;top:2278px;width:260px;text-align:center}
.step-ring{width:150px;height:150px;margin:0 auto;border-radius:50%;background:var(--white);box-shadow:0 2px 12px rgba(0,0,0,.18);position:relative}
.step-num{position:absolute;top:-22px;left:45px;width:60px;height:60px;border-radius:50%;background:var(--maroon-dark);color:var(--white);font-size:24px;font-weight:600;display:flex;align-items:center;justify-content:center}
.step-ring svg{position:absolute;left:45px;top:58px}
.step h4{font-size:19px;font-weight:600;margin-top:24px;line-height:1.55}
/* packages */
.packages-bg{position:absolute;top:2625px;left:0;width:1200px;height:655px;background:var(--grey-bg)}
.package{position:absolute;width:266px;background:var(--white);box-shadow:0 3px 12px rgba(0,0,0,.15)}
.package-head{height:80px;color:var(--white);font-size:20px;font-weight:600;display:flex;align-items:center;justify-content:center;text-align:center;line-height:1.3;clip-path:polygon(0 0,100% 0,100% 78%,50% 100%,0 78%)}
.package-head.dark{background:var(--ink)}
.package-head.red{background:var(--maroon-dark)}
.package ul{list-style:none;padding:24px 28px 10px 30px}
.package li{font-family:"Open Sans",sans-serif;font-size:12.5px;color:#444;line-height:1.55;margin-bottom:10px;padding-left:24px;position:relative}
.package li::before{content:"";position:absolute;left:2px;top:2px;width:6px;height:11px;border:solid var(--ink);border-width:0 3px 3px 0;transform:rotate(40deg)}
.price-row{position:absolute;bottom:0;left:0;width:100%;height:50px;display:flex;font-weight:600}
.price-row .paid{flex:1;display:flex;align-items:center;padding-left:42px;font-size:17px;color:#333;background:#f3f3f3}
.price-row .amount{width:136px;display:flex;align-items:center;justify-content:center;color:var(--white);font-size:17px}
/* testimonials */
.testimonial{position:absolute;top:3440px;width:296px;height:210px;background:var(--white);box-shadow:0 3px 14px rgba(0,0,0,.2);text-align:center;padding:66px 24px 0}
.testimonial p{font-family:"Open Sans",sans-serif;font-size:13px;line-height:1.75;color:var(--text)}
.avatar{position:absolute;top:3418px;width:90px;height:90px;border-radius:50%;border:4px solid var(--white);box-shadow:0 2px 8px rgba(0,0,0,.25);background:linear-gradient(180deg,#b89a86,#7a5a48)}
.reviewer{position:absolute;top:3694px;width:296px;text-align:center}
.reviewer h5{font-size:15px;font-weight:500;color:var(--maroon)}
.stars{color:var(--gold);font-size:17px;letter-spacing:2px;margin-top:6px}
/* footer */
.footer-bg{position:absolute;top:3800px;left:0;width:1200px;height:455px}
.footer-col{position:absolute;top:3922px;color:var(--white)}
.footer-col h6{font-size:18px;font-weight:600;margin-bottom:26px}
.footer-col ul{list-style:none;font-family:"Open Sans",sans-serif;font-size:13.5px;line-height:2.15}
.contact-line{display:flex;gap:16px;font-family:"Open Sans",sans-serif;font-size:14px;line-height:1.75;margin-bottom:26px}
.socials{display:flex;gap:12px;margin-top:6px}
.socials span{width:28px;height:28px;background:var(--white)}
.newsletter p{font-family:"Open Sans",sans-serif;font-size:13.5px;line-height:1.75;font-weight:600}
.email-field{margin-top:18px;width:266px;height:34px;background:var(--white);font-family:"Open Sans",sans-serif;font-size:11.5px;color:#777;padding:10px 12px}
.subscribe{margin-top:8px;width:266px;height:36px;background:var(--maroon-dark);font-size:15px;font-weight:600;display:flex;align-items:center;justify-content:center}
.copyright{position:absolute;top:4205px;width:1200px;text-align:center;color:var(--white);font-family:"Open Sans",sans-serif;font-size:13px}
</style>
</head>
<body>

<header class="site-header">
  <div class="brand"><span class="brand-square"></span>Meadow Kr Circle</div>
  <nav class="main-nav">
    <span class="active">Home</span><span>About Us</span><span>How To Start?</span><span>Packages</span><span>Contact Us</span>
    <svg width="18" height="18" viewBox="0 0 18 18"><circle cx="7" cy="7" r="5.5" fill="none" stroke="#444" stroke-width="2"/><line x1="11" y1="11" x2="16.5" y2="16.5" stroke="#444" stroke-width="2.4"/></svg>
  </nav>
</header>

<section class="hero">
  <div class="hero-photo" role="img" aria-label="Large family house with pitched roofs, trees and front lawn"></div>
  <div class="hero-title">
    <div class="hero-brand"><span class="brand-square"></span>Meadow Kr Circle</div>
    <div class="hero-sub">Short-Stay Management Proposal</div>
    <div class="hero-tag">Maximize Your Rental Income</div>
  </div>
  <div class="slider-dots"><span class="on"></span><span></span><span></span></div>
  <svg class="hero-swoosh" width="1200" height="110" viewBox="0 0 1200 110">
    <path d="M0 50 Q600 95 1200 20 L1200 110 L0 110Z" fill="var(--maroon)"/>
    <path d="M0 78 Q600 110 1200 55 L1200 110 L0 110Z" fill="var(--white)"/>
  </svg>
</section>

<section class="about">
  <div class="about-logo brand"><span class="brand-square"></span>Meadow Kr Circle</div>
  <div class="about-photo" role="img" aria-label="Modern white villa with pool at dusk"></div>
  <div class="about-box">
    <h2>About Us</h2>
    <p>We are a short-term rental management and provides hospitality services to help property owners maximize their rental income. Our goal is to help you reap the most from your rental income without you having to do any of the hard work such as handle all the particular renting problems on Stayluma, Roomvista, cleaning and dealing with tenants and guests.</p>
  </div>
</section>

<section class="services">
  <div class="services-band"></div>
  <h2 class="services-title">Our Hassle-Free Full Hospitality Service</h2>
  <article class="service-card" style="left:113px">
    <div class="photo" role="img" aria-label="Two people shaking hands" style="background:linear-gradient(135deg,#8a2a22,#c9a08c,#3b3f5a)"></div>
    <h3>Answering Enquiries,<br>Check-Ins / Outs</h3>
    <p>We will answer all guest's enquiries, meet them to handover key and verification check. We also provide 24hr on-call support.</p>
  </article>
  <article class="service-card" style="left:444px">
    <div class="photo" role="img" aria-label="Clean bright hallway" style="background:linear-gradient(180deg,#dbe5ec,#8fb3c8,#c7d2d8)"></div>
    <h3>Cleaning, Laundry and<br>Maintenance</h3>
    <p>We get the professional cleaning team to clean up the place after the guest checked-out every time.</p>
  </article>
  <article class="service-card" style="left:775px">
    <div class="photo" role="img" aria-label="Hands working at a desk with documents" style="background:linear-gradient(135deg,#3a2e24,#a7865e,#5c4a38)"></div>
    <h3>Marketing and<br>Optimization</h3>
    <p>We take professional photos and write persuasive copywriting to optimize your listing in order to get more booking.</p>
  </article>
</section>

<section class="steps">
  <h2 class="section-title" style="top:2098px">How To Start?</h2>
  <p class="steps-intro">The following steps are required in order to get<br>your place ready to start.</p>
  <div class="step" style="left:115px">
    <div class="step-ring"><span class="step-num">01</span>
      <svg width="60" height="60" viewBox="0 0 60 60" fill="none" stroke="var(--maroon)" stroke-width="2.5"><path d="M6 28 L30 10 L54 28"/><rect x="12" y="26" width="36" height="26"/><rect x="25" y="36" width="10" height="16"/><rect x="16" y="32" width="6" height="6"/><rect x="38" y="32" width="6" height="6"/></svg>
    </div>
    <h4>Getting The Required<br>Items</h4>
  </div>
  <div class="step" style="left:355px">
    <div class="step-ring"><span class="step-num">02</span>
      <svg width="60" height="60" viewBox="0 0 60 60" fill="none" stroke="var(--ink)" stroke-width="2.5"><path d="M6 30 L30 10 L54 30"/><path d="M13 25 V52 H47 V25"/><rect x="25" y="36" width="10" height="16"/></svg>
    </div>
    <h4>Renovation &amp;<br>Furnishing</h4>
  </div>
  <div class="step" style="left:595px">
    <div class="step-ring"><span class="step-num">03</span>
      <svg width="60" height="60" viewBox="0 0 60 60" fill="none" stroke="var(--ink)" stroke-width="2.5"><rect x="14" y="10" width="32" height="42" rx="2"/><line x1="20" y1="20" x2="40" y2="20"/><line x1="20" y1="28" x2="40" y2="28"/><line x1="20" y1="36" x2="34" y2="36"/><path d="M22 46 Q28 40 32 46 T40 44"/></svg>
    </div>
    <h4>Sign A Management<br>Agreement</h4>
  </div>
  <div class="step" style="left:840px">
    <div class="step-ring"><span class="step-num">04</span>
      <svg width="60" height="60" viewBox="0 0 60 60" fill="none" stroke="var(--ink)" stroke-width="2.5"><circle cx="40" cy="18" r="10"/><circle cx="40" cy="18" r="3"/><path d="M33 25 L10 50 M16 44 L21 49 M12 48 L16 52"/></svg>
    </div>
    <h4>Handover Keys &amp;<br>Access Cards, And<br>Relevant Information</h4>
  </div>
</section>

<section class="packages">
  <div class="packages-bg"></div>
  <h2 class="section-title" style="top:2688px">Our Packages</h2>
  <article class="package" style="left:175px;top:2800px;height:360px">
    <div class="package-head dark">Economic Package</div>
    <ul>
      <li>Full Height Day &amp; Night curtain</li><li>Main Entrance Door Grill</li><li>Supply &amp; Install LED Surface Light</li><li>Supply &amp; Install Down Light</li><li>Supply &amp; Install Ceiling Fan</li><li>Retractive Hanging Rack</li>
    </ul>
    <div class="price-row"><span class="paid">Paid</span><span class="amount" style="background:var(--ink)">RM7,950.00</span></div>
  </article>
  <article class="package" style="left:467px;top:2772px;height:410px">
    <div class="package-head red" style="height:86px">Furniture Package</div>
    <ul>
      <li>Sofa bed</li><li>Coffee table</li><li>Dining table set with 6-seaters</li><li>Ironing board</li><li>Microfiber pillows</li><li>Carpet rug</li>
    </ul>
    <div class="price-row"><span class="paid">Paid</span><span class="amount" style="background:var(--maroon-dark)">RM9,900.00</span></div>
  </article>
  <article class="package" style="left:758px;top:2800px;height:360px">
    <div class="package-head dark">Curtain, Soft touch<br>&amp; MISC</div>
    <ul>
      <li>Bed linens x 3 sets</li><li>Cooking utensils, Cutlery and Kitchenware</li><li>Designer standing lamp</li><li>Power saving cut-off system</li><li>Bathroom linens and accessories</li>
    </ul>
    <div class="price-row"><span class="paid">Paid</span><span class="amount" style="background:var(--ink)">RM4,500.00</span></div>
  </article>
</section>

<section class="testimonials">
  <h2 class="section-title" style="top:3340px">Testimonials</h2>
  <div class="testimonial" style="left:115px"><p>Lorem ipsum dolor sit amet, consectetur adipiscing elit, sed do eiusmod tempor incididunt ut</p></div>
  <div class="testimonial" style="left:450px"><p>Lorem ipsum dolor sit amet, consectetur adipiscing elit, sed do eiusmod tempor incididunt ut</p></div>
  <div class="testimonial" style="left:785px"><p>Lorem ipsum dolor sit amet, consectetur adipiscing elit, sed do eiusmod tempor incididunt ut</p></div>
  <div class="avatar" style="left:218px" role="img" aria-label="Portrait of Lena Marwick"></div>
  <div class="avatar" style="left:553px" role="img" aria-label="Portrait of Rosalind Mae Thornby"></div>
  <div class="avatar" style="left:888px;background:linear-gradient(180deg,#c8b39c,#3d4e66)" role="img" aria-label="Portrait of Corin Ashdale"></div>
  <div class="reviewer" style="left:115px;top:3694px"><h5>Lena Marwick</h5><div class="stars">★★★★★</div></div>
  <div class="reviewer" style="left:450px;top:3688px"><h5>Rosalind Mae Thornby</h5><div class="stars">★★★★★</div></div>
  <div class="reviewer" style="left:785px;top:3682px"><h5>Corin Ashdale</h5><div class="stars">★★★★★</div></div>
</section>

<footer>
  <svg class="footer-bg" width="1200" height="455" viewBox="0 0 1200 455">
    <path d="M0 80 Q600 50 1200 0 L1200 455 L0 455Z" fill="var(--maroon)"/>
    <path d="M0 100 Q600 85 1200 40 L1200 455 L0 455Z" fill="var(--white)"/>
    <path d="M0 110 Q600 100 1200 55 L1200 455 L0 455Z" fill="var(--maroon-dark)"/>
    <path d="M0 125 Q600 110 1200 75 L1200 455 L0 455Z" fill="var(--footer)"/>
  </svg>
  <div class="footer-col" style="left:110px;width:280px">
    <h6>Contact Us</h6>
    <div class="contact-line"><svg width="20" height="26" viewBox="0 0 20 26" style="flex:none;margin-top:6px"><path d="M10 1 C4 1 1 5 1 10 C1 16 10 25 10 25 C10 25 19 16 19 10 C19 5 16 1 10 1Z" fill="#fff"/><circle cx="10" cy="10" r="3.5" fill="#0d0d0d"/></svg><span>L14-06 Orchid Residence, Jalan Seroja, Taman Melati, 81200 Johor Bahru</span></div>
    <div class="contact-line" style="align-items:center"><svg width="22" height="20" viewBox="0 0 22 20"><path d="M3 12 V10 A8 8 0 0 1 19 10 V12" fill="none" stroke="#fff" stroke-width="2"/><rect x="1" y="11" width="5" height="7" rx="1" fill="#fff"/><rect x="16" y="11" width="5" height="7" rx="1" fill="#fff"/></svg><span>+60 7 555 0142</span></div>
    <div class="socials"><span></span><span></span><span></span><span></span></div>
  </div>
  <div class="footer-col" style="left:415px">
    <h6>Quick Links</h6>
    <ul><li>Home</li><li>About Us</li><li>How To Start?</li><li>Packages</li><li>Contact Us</li></ul>
  </div>
  <div class="footer-col" style="left:612px">
    <h6>Other Links</h6>
    <ul><li>Privacy Policy</li><li>Terms &amp; Conditions</li></ul>
  </div>
  <div class="footer-col newsletter" style="left:818px;width:270px">
    <h6>Newsletter</h6>
    <p>But I must explain to you how all this mistaken idea of denouncing pleasure and praising.</p>
    <div class="email-field">Enter your email address</div>
    <div class="subscribe">Subscribe</div>
  </div>
  <div class="copyright">© 2018 Copyrights | All Rights Reserved</div>
</footer>

</body>
</html>
```